Informational Site for Advanced Chemistry R&D

The company develops oxidation chemistry for air, water, fuel pollution controls. The site has been prototyped at www.velquaresearch.example. Take a look. Now, the task is to design it for eye-catching beauty with use of color, on-page scroll-driven color transition and parallax effects. Should capture the themes: high technology, wow it's beautiful, modern, uncluttered, clean urban environment.

Target Market(s)

China Environmentally Conscious Government and Industry,

Industry/Entity Type

It Company

Number of Pages Required

3 page

Font styles to use
Sans Serif

Requirements
Must have
• Parallax effects, desktop compatible, Rich, Modern, Simple, Graphic
Nice to have
• Mobile Phone Compatible
Should not have
• Flash, or anything that is slow to load or requires high bandwidth

```html
<!DOCTYPE html>
<html lang="en">
<head>
<meta charset="utf-8">
<title>Velqua Research — Advanced Oxidation Science</title>
<link href="https://fonts.googleapis.com/css2?family=Raleway:wght@400;500;600;700&family=Open+Sans:ital,wght@0,400;0,600;1,400&display=swap" rel="stylesheet">
<style>
:root{
  --teal:#1fa9b8;
  --teal-dark:#1a7fa6;
  --blue-head:#1f7fb8;
  --page:#f1f1f1;
  --ink:#555;
  --ink-soft:#777;
  --night:#0d1117;
  --ocean:#1b6e9f;
  --ocean-deep:#12466e;
  --footer:#323436;
  --field:#3f4245;
  --white:#fff;
}
*{box-sizing:border-box;margin:0;padding:0}
html,body{width:1200px;height:3098px;overflow:hidden}
body{background:var(--page);font-family:"Open Sans",Arial,sans-serif;color:var(--ink)}
.page{position:relative;width:1200px;height:3098px;overflow:hidden;
  background:var(--page);
  background-image:radial-gradient(#e4e4e4 1px,transparent 1px);background-size:14px 14px}
.backdrop{position:absolute;left:0;top:0}
.abs{position:absolute}
h1,h2,h3{font-family:"Raleway",Arial,sans-serif;font-weight:500}

/* header */
.site-header{position:absolute;left:0;top:0;width:1200px;height:108px;background:var(--white);border-bottom:3px solid var(--teal)}
.brand{position:absolute;left:100px;top:30px;display:flex;align-items:center;gap:10px;font-family:"Raleway",sans-serif;font-weight:700;font-size:28px;color:var(--teal-dark)}
.brand-dot{width:22px;height:22px;border-radius:50%;background:var(--teal)}
.nav{position:absolute;top:54px;left:0;width:1200px;font-family:"Raleway",sans-serif;font-size:13px;letter-spacing:.5px;color:#777}
.nav a{position:absolute;text-decoration:none;color:inherit}
.nav .active{color:var(--teal-dark);font-weight:600}
.nav .active::before{content:"";position:absolute;left:-8px;top:-18px;width:46px;height:46px;border-radius:50%;border:1px solid #d7e9ef}

/* hero */
.hero-title{position:absolute;left:650px;top:338px;width:455px;font-family:"Raleway",sans-serif;font-weight:600;font-size:31px;line-height:44px;color:var(--white);text-align:justify;text-align-last:justify}
.hero-name{position:absolute;left:368px;top:428px;font-family:"Raleway",sans-serif;font-weight:700;font-size:44px;color:var(--teal)}
.dots{position:absolute;left:856px;top:600px;display:flex;gap:14px}
.dots span{width:10px;height:10px;border-radius:50%;background:rgba(255,255,255,.55)}
.dots span.on{background:var(--white)}

/* welcome */
.section-title{position:absolute;left:0;width:1200px;text-align:center;font-size:29px;letter-spacing:.5px}
.welcome-title{top:770px;color:var(--blue-head)}
.welcome-text{position:absolute;left:170px;top:826px;width:860px;text-align:center;font-size:13.5px;line-height:22px;color:#666}
.feature{position:absolute;top:905px;width:300px;height:100px}
.feature-icon{position:absolute;left:0;top:0;width:90px;height:90px}
.feature h3{position:absolute;left:102px;top:0;font-size:20px;color:var(--teal);font-weight:500}
.feature p{position:absolute;left:102px;top:32px;width:210px;font-size:12px;line-height:21px;color:#777;text-align:justify}

/* oxidation */
.ox-title{top:1182px;color:var(--white)}
.ox-text{position:absolute;left:0;width:1200px;text-align:center;color:#e6e6e6}
.ox-lead{top:1241px;font-size:16px;line-height:26px}
.ox-bullet{position:absolute;top:1321px;font-size:15px;color:#eee}
.ox-bullet::before{content:"";position:absolute;left:-34px;top:8px;width:7px;height:7px;border-radius:50%;background:#fff}
.ox-after{top:1371px;font-size:14px;line-height:27px}

/* solutions */
.sol-title{top:1595px;color:var(--white)}
.card{position:absolute;top:1671px;width:246px;height:357px;background:rgba(236,243,249,.93)}
.card-photo{width:246px;height:183px;display:block}
.card h3{font-family:"Open Sans",sans-serif;font-weight:600;font-size:14.5px;color:#333;margin:22px 0 0 20px}
.card p{margin:8px 18px 0 20px;font-size:11.5px;line-height:19px;color:#666;text-align:justify}
.card .more{position:absolute;right:26px;bottom:22px;font-size:11.5px;color:var(--teal-dark)}

/* partners */
.partners-title{top:2210px;color:var(--blue-head)}
.partner{position:absolute;top:2276px;width:240px;height:146px;background:var(--white);border:1px solid #e3e3e3;text-align:center}
.partner .mark{position:absolute;left:50%;top:26px;transform:translateX(-50%)}
.partner .mark-name{position:absolute;left:0;top:60px;width:100%;font-family:"Raleway",sans-serif;font-weight:700;font-size:15px;color:var(--teal-dark)}
.partner .label{position:absolute;left:0;top:102px;width:100%;font-size:15.5px;color:#555}

/* contact */
.contact-title{top:2603px;color:var(--white);letter-spacing:1px}
.addr-head{position:absolute;left:100px;top:2694px;display:flex;align-items:center;gap:16px;font-family:"Raleway",sans-serif;font-weight:700;font-size:13px;color:var(--white)}
.addr{position:absolute;left:128px;top:2745px;font-style:italic;font-size:14px;line-height:31px;color:#eee}
.social{position:absolute;left:124px;top:2886px;display:flex;gap:34px}
.social span{width:14px;height:14px;border-radius:50%;background:#e9e9e9}
.field{position:absolute;background:var(--field);color:#999;font-size:13px;padding:13px 16px}
.field.focus{background:#2b2d2f;border-top:2px solid var(--teal);color:#eee}
.send{position:absolute;left:950px;top:2990px;width:144px;height:46px;background:var(--teal);border-radius:4px;color:var(--white);font-size:15px;text-align:center;line-height:46px}
.copy{position:absolute;left:107px;top:3014px;font-size:12px;color:#ddd;letter-spacing:.3px}
.copy b{font-weight:400;color:var(--teal)}
</style>
</head>
<body>
<div class="page">

  <!-- background bands -->
  <svg class="backdrop" width="1200" height="3098" viewBox="0 0 1200 3098" aria-hidden="false">
    <defs>
      <linearGradient id="heroGrad" x1="0" y1="0" x2="1" y2="1">
        <stop offset="0" stop-color="#8fa3b3"/>
        <stop offset=".35" stop-color="#4a6377"/>
        <stop offset=".7" stop-color="#2d3d4e"/>
        <stop offset="1" stop-color="#8a6b4c"/>
      </linearGradient>
      <radialGradient id="nightGrad" cx=".5" cy=".45" r=".7">
        <stop offset="0" stop-color="#2a2f36"/>
        <stop offset="1" stop-color="#07090c"/>
      </radialGradient>
      <linearGradient id="oceanGrad" x1="0" y1="0" x2="0" y2="1">
        <stop offset="0" stop-color="#2a8fc4"/>
        <stop offset=".5" stop-color="#1b6a9c"/>
        <stop offset="1" stop-color="#124a75"/>
      </linearGradient>
    </defs>
    <path role="img" aria-label="Photo of a gloved hand holding a glowing glass disc in front of warm bokeh lights and binary data"
      d="M0,111 H1200 V560 C1000,520 850,650 600,640 C350,630 200,560 0,600 Z" fill="url(#heroGrad)"/>
    <path role="img" aria-label="Photo of a dark starry space scene"
      d="M0,1040 C300,1000 500,1130 800,1090 C1000,1060 1100,1010 1200,1020 L1200,1480 C1000,1440 700,1520 400,1470 C200,1440 100,1480 0,1490 Z" fill="url(#nightGrad)"/>
    <path role="img" aria-label="Blue background with a faint molecular network"
      d="M0,1470 C250,1420 500,1500 800,1450 C1000,1420 1100,1440 1200,1430 L1200,2170 C1000,2160 800,2080 500,2100 C300,2110 150,2060 0,2060 Z" fill="url(#oceanGrad)"/>
    <path d="M0,2450 C250,2440 400,2580 700,2540 C900,2510 1050,2560 1200,2560 L1200,3098 L0,3098 Z" fill="var(--footer)"/>
  </svg>

  <header class="site-header">
    <div class="brand"><span class="brand-dot"></span>Velqua</div>
    <nav class="nav">
      <a class="active" style="left:604px">HOME</a>
      <a style="left:718px">TECHNOLOGY</a>
      <a style="left:886px">PRODUCTS</a>
      <a style="left:1034px">CONTACT</a>
    </nav>
  </header>

  <div class="hero-name">Velqua</div>
  <h1 class="hero-title">Advanced Oxidation Science for Environmental Pollution Management</h1>
  <div class="dots"><span></span><span class="on"></span><span></span></div>

  <h2 class="section-title welcome-title">WELCOME TO VELQUA SERVICE</h2>
  <p class="welcome-text">But I must explain to you how all this mistaken idea of denouncing pleasure and praising pain was born and I will give you a complete account of the system, and expound the actual teachings of the great explorer of the truth, the master-builder of human .</p>

  <div class="feature" style="left:96px">
    <svg class="feature-icon" viewBox="0 0 90 90"><circle cx="45" cy="45" r="43" fill="none" stroke="#1fa9b8" stroke-width="1.5"/><circle cx="45" cy="45" r="36" fill="none" stroke="#cfe9ee" stroke-width="1"/><path d="M45,28 C52,40 56,46 56,52 A11,11 0 0 1 34,52 C34,46 38,40 45,28 Z" fill="#1fa9b8"/></svg>
    <h3>WATER</h3>
    <p>Duis aute irure dolor in reprehenderit in voluptate velit esse cillum dolore eu fugiat nulla pariatur.</p>
  </div>
  <div class="feature" style="left:443px">
    <svg class="feature-icon" viewBox="0 0 90 90"><circle cx="45" cy="45" r="43" fill="none" stroke="#1fa9b8" stroke-width="1.5"/><circle cx="45" cy="45" r="36" fill="none" stroke="#cfe9ee" stroke-width="1"/><path d="M26,46 L64,30 L52,62 L45,50 Z M45,50 L64,30" fill="none" stroke="#1fa9b8" stroke-width="2.5" stroke-linejoin="round"/></svg>
    <h3>AIR</h3>
    <p>Duis aute irure dolor in reprehenderit in voluptate velit esse cillum dolore eu fugiat nulla pariatur.</p>
  </div>
  <div class="feature" style="left:790px">
    <svg class="feature-icon" viewBox="0 0 90 90"><circle cx="45" cy="45" r="43" fill="none" stroke="#1fa9b8" stroke-width="1.5"/><circle cx="45" cy="45" r="36" fill="none" stroke="#cfe9ee" stroke-width="1"/><path d="M45,24 C56,38 62,46 62,54 A17,17 0 0 1 28,54 C28,46 34,38 45,24 Z" fill="#1fa9b8"/><text x="45" y="58" text-anchor="middle" font-family="Open Sans, sans-serif" font-size="12" fill="#fff">bio</text></svg>
    <h3>FUEL</h3>
    <p>Duis aute irure dolor in reprehenderit in voluptate velit esse cillum dolore eu fugiat nulla pariatur.</p>
  </div>

  <h2 class="section-title ox-title">ADVANCED OXIDATION</h2>
  <p class="ox-text ox-lead">Advanced Oxidation refers to a &nbsp;variety of techniques employing the Hydroxyl Radical,<br>an energetic, highly reactive cousin of the water molecule:</p>
  <span class="ox-bullet" style="left:272px">To add oxygen to inorganic molecules</span>
  <span class="ox-bullet" style="left:640px">To remove hydrogen from organic molecules</span>
  <p class="ox-text ox-after">These transformations convert important industrial contaminants into reactive forms<br>that can be captured or that disintegrate into harmless end products.</p>

  <h2 class="section-title sol-title">SOLUTIONS</h2>

  <article class="card" style="left:99px">
    <svg class="card-photo" role="img" aria-label="Photo of refinery pipes and towers"><defs><linearGradient id="p1" x1="0" y1="0" x2="0" y2="1"><stop offset="0" stop-color="#c8cdd2"/><stop offset="1" stop-color="#2e3338"/></linearGradient></defs><rect width="246" height="183" fill="url(#p1)"/></svg>
    <h3>Fuel Oil Desulfurization</h3>
    <p>Our proprietary low temperature and pressure advanced oxidation catalytic process reliably removes sulfur from diesel transportation fuel at less</p>
    <span class="more">[ Learn More ]</span>
  </article>
  <article class="card" style="left:351px">
    <svg class="card-photo" role="img" aria-label="Photo of a worker handling blue chemical drums"><defs><linearGradient id="p2" x1="0" y1="0" x2="0" y2="1"><stop offset="0" stop-color="#5d7fa6"/><stop offset="1" stop-color="#1d3e73"/></linearGradient></defs><rect width="246" height="183" fill="url(#p2)"/></svg>
    <h3>Volatile Organic Compunds</h3>
    <p>Alkanes, alkenes, halogenated hydrocarbons, aromatic hydrocarbons, esters, aldehydes, polycyclic aromatic hydrocarbons.</p>
    <span class="more">[ Learn More ]</span>
  </article>
  <article class="card" style="left:605px">
    <svg class="card-photo" role="img" aria-label="Photo of smokestacks releasing flue gas"><defs><linearGradient id="p3" x1="0" y1="0" x2="0" y2="1"><stop offset="0" stop-color="#6b7088"/><stop offset=".6" stop-color="#8d8fa0"/><stop offset="1" stop-color="#23242c"/></linearGradient></defs><rect width="246" height="183" fill="url(#p3)"/></svg>
    <h3>Flue Gas Scrubbing</h3>
    <p>Desulfurization and denitrification using our proprietary flue gas advanced oxidation catalytic process (FGAOC). Sulfur and nitrogen</p>
    <span class="more">[ Learn More ]</span>
  </article>
  <article class="card" style="left:857px">
    <svg class="card-photo" role="img" aria-label="Photo of a pipe discharging wastewater into a river"><defs><linearGradient id="p4" x1="0" y1="0" x2="0" y2="1"><stop offset="0" stop-color="#4f6a3a"/><stop offset=".55" stop-color="#8b8a6a"/><stop offset="1" stop-color="#9a7a52"/></linearGradient></defs><rect width="246" height="183" fill="url(#p4)"/></svg>
    <h3>Wastewater Treatment</h3>
    <p>Photoelectrocatalysed (PEC) anodic oxidation removes soluble organics. Novel anode design using our proprietary nano-carbon surface</p>
    <span class="more">[ Learn More ]</span>
  </article>

  <h2 class="section-title partners-title">PARTNERS</h2>
  <div class="partner" style="left:99px">
    <svg class="mark" width="34" height="34"><circle cx="17" cy="17" r="16" fill="#1fa9b8"/></svg>
    <span class="mark-name">Velqua Systems</span>
    <span class="label">Our sales partner in China</span>
  </div>
  <div class="partner" style="left:353px">
    <svg class="mark" width="56" height="56" style="top:24px"><circle cx="28" cy="28" r="26" fill="#e0632a"/></svg>
    <span class="label">Our construction partner</span>
  </div>
  <div class="partner" style="left:607px">
    <svg class="mark" width="62" height="62" style="top:22px"><circle cx="31" cy="31" r="29" fill="none" stroke="#2e5c95" stroke-width="3"/></svg>
    <span class="label">Our technology partner</span>
  </div>
  <div class="partner" style="left:861px">
    <svg class="mark" width="62" height="62" style="top:22px"><circle cx="31" cy="31" r="29" fill="#b2232b"/></svg>
    <span class="label">Our technology partner</span>
  </div>

  <h2 class="section-title contact-title">CONTACT US</h2>
  <div class="addr-head">
    <svg width="14" height="20" viewBox="0 0 14 20"><path d="M7,0 A7,7 0 0 1 14,7 C14,12 7,20 7,20 C7,20 0,12 0,7 A7,7 0 0 1 7,0 Z" fill="#1fa9b8"/><circle cx="7" cy="7" r="2.6" fill="#323436"/></svg>
    ADDRESS
  </div>
  <address class="addr">415 Harbor Lane, Suite 12<br>Fairview, ST 00000<br>(555) 013-0142<br>Mara Ellison</address>
  <div class="social"><span></span><span></span><span></span><span></span></div>

  <div class="field focus" style="left:448px;top:2691px;width:310px;height:42px">Alan |</div>
  <div class="field" style="left:783px;top:2691px;width:308px;height:42px">Email</div>
  <div class="field" style="left:448px;top:2761px;width:310px;height:42px">Telephone</div>
  <div class="field" style="left:783px;top:2761px;width:308px;height:42px">Subject</div>
  <div class="field" style="left:448px;top:2829px;width:643px;height:128px">Message</div>
  <div class="send">Send Now</div>

  <p class="copy">2016 ©<b>VELQUA SERVICE</b>. ALL RIGHTS RESERVED.</p>
</div>
</body>
</html>
```